Custom Cabinet Shop Needs a website design

Hi,
We need a website for a Custom Cabinet Shop and Cabinet parts manufacturing business.
The business has two sides to it. One side provides custom Kitchens, vanities, entertainment units, offices and what not to homeowners and contractors.
The 2nd side of the business provides built to order cabinet boxes and other parts required to put together a project to other cabinet shops, small contractors looking to install there own cabinets.
Website will need a Gallery to display work.
Color scheme to go well with logo.
current website is www.brambleoakcustomcabinets.com
being changed to www.brambleoak.ca
Logo Included in attached files.
Tagline "Joinery with Spirit"
Mission Statement "Our passion is to deliver inspired cabinetry solutions to suit all your needs, supported by our phenomenal star class customer service"
The website should convey quality and professionalism.
Thank you.
Homeowners/ Contractors
Entertainment

```html
<!DOCTYPE html>
<html lang="en">
<head>
<meta charset="utf-8">
<title>Brambleoak Custom Cabinets</title>
<link href="https://fonts.googleapis.com/css2?family=Raleway:wght@400;500;600;700;800&family=Noto+Serif:ital@1&family=Dosis:wght@500&display=swap" rel="stylesheet">
<style>
:root{
  --orange:#f0601f;
  --orange-light:#f39a5a;
  --orange-deep:#d9561a;
  --date-orange:#f7941d;
  --dark:#1d1d1d;
  --dark-2:#2c2c2c;
  --footer:#161616;
  --footer-bottom:#0b0b0b;
  --text:#555;
  --heading:#333;
  --rule:#bdbdbd;
  --white:#fff;
  --muted:#a9a9a9;
}
*{margin:0;padding:0;box-sizing:border-box}
html,body{width:1060px;height:1200px;overflow:hidden;background:var(--white)}
body{position:relative;font-family:"Raleway",Arial,sans-serif;color:var(--text);font-variant-numeric:lining-nums}
.abs{position:absolute}

/* header */
.site-header{position:absolute;left:0;top:0;width:1060px;height:117px}
.nav-bar{position:absolute;left:0;top:71px;width:1060px;height:46px;background:linear-gradient(#3a3a3a,#1e1e1e)}
.logo-tab{position:absolute;left:0;top:0}
.brand{position:absolute;left:160px;top:44px;font-weight:800;font-size:26px;letter-spacing:1px;color:var(--dark);display:flex;align-items:center;gap:8px}
.brand-mark{width:14px;height:14px;background:var(--orange)}
.call{position:absolute;left:820px;top:15px}
.call small{display:block;font-size:13px;font-weight:500;color:var(--heading)}
.call strong{display:block;font-size:19px;font-weight:700;color:var(--orange);margin-top:1px}
.call-icon{position:absolute;left:778px;top:18px}
.main-nav{position:absolute;top:71px;left:0;height:46px;width:1060px}
.main-nav a{position:absolute;top:15px;font-size:13px;font-weight:500;color:var(--white);text-decoration:none;letter-spacing:.2px}
.main-nav .sep{position:absolute;top:14px;color:#777;font-size:16px}

/* hero */
.hero-bg{position:absolute;left:0;top:117px}
.hero-photo{position:absolute;left:122px;top:117px;width:819px;height:325px;background:linear-gradient(160deg,#7c6f62 0%,#b8ab9b 35%,#8e8174 60%,#4a3d33 100%)}
.hero-caption{position:absolute;font-family:"Noto Serif",Georgia,serif;font-style:italic;color:var(--white);text-align:center}
.cap-1{left:343px;top:254px;width:366px;height:51px;background:var(--orange);font-size:32px;line-height:51px}
.cap-2{left:271px;top:311px;width:511px;height:48px;background:rgba(20,20,20,.85);font-size:31px;line-height:48px}
.dots{position:absolute;left:497px;top:469px;display:flex;gap:7px}
.dots span{width:11px;height:11px;border-radius:50%;background:#2a2a2a}
.dots span.active{background:#f2c7b0}

/* thumbs */
.thumb{position:absolute;top:532px;width:175px;height:115px;border:1px solid #ddd}
.thumb-1{left:150px;background:linear-gradient(150deg,#d8d0c6,#6a4a36 60%,#2a201b)}
.thumb-2{left:343px;background:linear-gradient(150deg,#4a4a4a,#2c2c2c)}
.thumb-3{left:535px;background:linear-gradient(150deg,#d6d3cb,#3a2a24 55%,#cfccc4)}
.thumb-4{left:739px;background:linear-gradient(150deg,#e9e4d8,#8a7a68 55%,#5a4438)}
.thumb-label{position:absolute;left:0;bottom:0;width:100%;height:31px;background:var(--orange);color:var(--white);font-family:"Dosis",sans-serif;font-weight:500;font-size:21px;text-align:center;line-height:31px}
.arrow{position:absolute;top:590px}

/* content */
.section-title{position:absolute;font-size:19px;font-weight:600;color:var(--heading);letter-spacing:.2px}
.section-title em{font-style:normal;color:var(--orange)}
.title-rule{position:absolute;height:2px;background:var(--rule)}
.slash{position:absolute}
.about-text{position:absolute;left:123px;top:733px;width:518px;font-size:12.4px;line-height:21.2px;color:var(--text)}
.news-item{position:absolute;left:655px;width:290px}
.news-date{position:absolute;left:0;top:0;width:49px}
.news-date .day{height:30px;background:var(--date-orange);color:var(--white);font-size:19px;text-align:center;line-height:31px;position:relative}
.news-date .day::after{content:"";position:absolute;right:-5px;top:10px;width:9px;height:9px;background:var(--date-orange);transform:rotate(45deg)}
.news-date .month{height:26px;background:#3a3a3a;color:var(--white);font-size:11.5px;text-align:center;line-height:26px}
.news-title{position:absolute;left:63px;top:-3px;font-size:15.5px;font-weight:500;color:var(--heading);white-space:nowrap}
.news-text{position:absolute;left:63px;top:23px;width:232px;font-size:11.6px;line-height:19px;color:var(--text)}

/* footer */
.site-footer{position:absolute;left:0;top:910px;width:1060px;height:238px;background:var(--footer)}
.footer-bottom{position:absolute;left:0;top:1148px;width:1060px;height:52px;background:var(--footer-bottom)}
.foot-col{position:absolute;top:942px}
.foot-col h3{font-size:15.5px;font-weight:500;color:var(--white);height:28px}
.foot-col .rule{height:1px;background:#555;margin-bottom:21px}
.foot-col ul{list-style:none}
.foot-col li{font-size:12.6px;color:var(--muted);height:23px;padding-left:14px;position:relative;white-space:nowrap}
.foot-col li::before{content:"›";position:absolute;left:0;top:-2px;font-size:14px;color:#888}
.contact-line{position:absolute;font-size:12.6px;color:var(--muted);line-height:19.5px}
.contact-phone{position:absolute;left:544px;top:1050px;font-size:16px;color:var(--muted);font-weight:500}
.foot-brand{position:absolute;left:750px;top:1020px;font-weight:800;font-size:21px;letter-spacing:1px;color:var(--white);display:flex;align-items:center;gap:7px}
.copyright{position:absolute;left:115px;top:1166px;font-size:12.6px;color:#bdbdbd}
.legal{position:absolute;right:115px;top:1166px;font-size:12.6px;color:#bdbdbd}
.legal span{margin:0 12px;color:#777}
</style>
</head>
<body>

<header class="site-header">
  <div class="nav-bar"></div>
  <svg class="logo-tab" width="400" height="113" viewBox="0 0 400 113">
    <polygon points="122,70 394,70 374,112 142,112" fill="#fff"/>
  </svg>
  <div class="brand"><span class="brand-mark"></span>Brambleoak</div>
  <svg class="call-icon" width="34" height="36" viewBox="0 0 34 36">
    <path d="M6 4 L12 3 L15 11 L11 14 Q14 22 20 26 L24 22 L31 26 L30 32 Q26 35 20 33 Q6 26 3 11 Q3 6 6 4Z" fill="#1d1d1d"/>
    <path d="M19 5 Q27 7 29 15" stroke="#f0601f" stroke-width="2.2" fill="none"/>
    <path d="M19 10 Q23 11 24 15" stroke="#f0601f" stroke-width="2.2" fill="none"/>
  </svg>
  <div class="call"><small>CALL US TODAY</small><strong>555-283-4719</strong></div>
  <nav class="main-nav">
    <a style="left:407px">HOME</a><span class="sep" style="left:472px">/</span>
    <a style="left:507px">GALLERY</a><span class="sep" style="left:588px">/</span>
    <a style="left:623px">SERVICES</a><span class="sep" style="left:714px">/</span>
    <a style="left:748px">WARRANTY</a><span class="sep" style="left:846px">/</span>
    <a style="left:880px">CONTACT</a>
  </nav>
</header>

<svg class="hero-bg" width="1060" height="450" viewBox="0 117 1060 450">
  <defs>
    <linearGradient id="sideGlow" x1="0" y1="0" x2="1" y2="1">
      <stop offset="0" stop-color="#f3a468"/>
      <stop offset="1" stop-color="#e46a26"/>
    </linearGradient>
  </defs>
  <polygon points="0,117 1060,117 1060,428 941,442 122,442 0,428" fill="url(#sideGlow)"/>
  <rect x="122" y="430" width="819" height="135" fill="#262626"/>
  <polygon points="122,445 360,471 530,498 700,471 941,437 941,440 700,474 530,500 360,474 122,448" fill="#f0601f"/>
  <polygon points="360,471 460,452 600,452 700,471 530,498" fill="#f0601f"/>
</svg>
<div class="hero-photo" role="img" aria-label="Photo of a bright custom kitchen with white cabinets, granite island and bar stools"></div>
<div class="hero-caption cap-1">Joinery with Spirit</div>
<div class="hero-caption cap-2">Custom Cabinet Design Company</div>
<div class="dots"><span></span><span class="active"></span><span></span><span></span></div>

<svg class="arrow" style="left:120px" width="16" height="24" viewBox="0 0 16 24"><path d="M12 2 L3 12 L12 22" stroke="#888" stroke-width="2.5" fill="none"/></svg>
<div class="thumb thumb-1" role="img" aria-label="Photo of a kitchen with dark wood island"></div>
<div class="thumb thumb-2" role="img" aria-label="Photo of a residential kitchen"><div class="thumb-label">Residential</div></div>
<div class="thumb thumb-3" role="img" aria-label="Photo of a dark wood entertainment unit"></div>
<div class="thumb thumb-4" role="img" aria-label="Photo of a dining area with wooden table"></div>
<svg class="arrow" style="left:928px" width="16" height="24" viewBox="0 0 16 24"><path d="M4 2 L13 12 L4 22" stroke="#888" stroke-width="2.5" fill="none"/></svg>

<svg class="slash" style="left:118px;top:688px" width="16" height="32"><line x1="3" y1="2" x2="13" y2="30" stroke="#f0601f" stroke-width="2"/></svg>
<h2 class="section-title" style="left:141px;top:688px"><em>WHO</em> WE ARE</h2>
<div class="title-rule" style="left:132px;top:716px;width:504px"></div>
<p class="about-text">Lorem Ipsum is simply dummy text of the printing and typesetting industry. Lorem Ipsum has been the industry's standard dummy text ever since the 1500s, when an unknown printer took a galley of type and scrambled it to make a type specimen book. It has sur&shy;vived not only five centuries, but also the leap into electronic typesetting, remaining essentially unchanged. It was popularised in the 1960s with the release of Lettrafix sheets containing Lorem Ipsum passages, and more recently with desktop publishing software like Pagecraft including versions of Lorem Ipsum.</p>

<svg class="slash" style="left:651px;top:688px" width="16" height="32"><line x1="3" y1="2" x2="13" y2="30" stroke="#f0601f" stroke-width="2"/></svg>
<h2 class="section-title" style="left:676px;top:688px"><em>LATEST</em> NEWS</h2>
<div class="title-rule" style="left:665px;top:716px;width:278px"></div>

<article class="news-item" style="top:741px">
  <div class="news-date"><div class="day">01</div><div class="month">MAR</div></div>
  <h3 class="news-title">Lorem Ipsum is simply</h3>
  <p class="news-text">Lorem Ipsum is simply dummy text of the printing and typesetting industry.</p>
</article>
<article class="news-item" style="top:818px">
  <div class="news-date"><div class="day">01</div><div class="month">MAR</div></div>
  <h3 class="news-title">Lorem Ipsum is simply</h3>
  <p class="news-text">Lorem Ipsum is simply dummy text of the printing and typesetting industry.</p>
</article>

<footer class="site-footer"></footer>
<div class="foot-col" style="left:119px;width:157px">
  <h3>Who We Are</h3><div class="rule"></div>
  <ul><li>Home</li><li>Gallery</li><li>Services</li><li>Warranty</li><li>Contact</li></ul>
</div>
<div class="foot-col" style="left:292px;width:193px">
  <h3>Our Services</h3><div class="rule"></div>
  <ul><li>Lorem Ipsum Dolor Sit Amet</li><li>Typesetting Industry</li><li>Have been Sent in Lorem</li><li>Services Which Done</li><li>Inside Vehicula Quis</li></ul>
</div>
<div class="foot-col" style="left:519px;width:193px">
  <h3>Contact Us</h3><div class="rule"></div>
</div>
<svg class="abs" style="left:521px;top:991px" width="14" height="18" viewBox="0 0 14 18"><path d="M7 1 A6 6 0 0 1 13 7 Q13 11 7 17 Q1 11 1 7 A6 6 0 0 1 7 1Z" fill="#888"/><circle cx="7" cy="7" r="2.3" fill="#161616"/></svg>
<div class="contact-line" style="left:545px;top:990px">4820 Willow Bend Road<br>Cedar Hollow, Alberta<br>T0X 1A0</div>
<svg class="abs" style="left:520px;top:1049px" width="16" height="18" viewBox="0 0 16 18"><path d="M3 1 L7 1 L8 6 L6 7 Q7 11 10 13 L12 11 L15 13 L14 17 Q6 16 2 5Z" fill="#888"/></svg>
<div class="contact-phone">555-962-3058</div>
<svg class="abs" style="left:520px;top:1087px" width="18" height="13" viewBox="0 0 18 13"><rect x="0.5" y="0.5" width="17" height="12" fill="none" stroke="#888"/><path d="M1 1 L9 7 L17 1" stroke="#888" fill="none"/></svg>
<div class="contact-line" style="left:545px;top:1082px">sales@brambleoakcustomcabinets.com</div>
<div class="foot-brand"><span class="brand-mark"></span>Brambleoak</div>

<div class="footer-bottom"></div>
<div class="copyright">copyright©2015.Bramble Oak Cabinet. All Rights Reserved</div>
<div class="legal">Privacy Policy<span>|</span>Terms &amp; Conditions</div>

</body>
</html>
```